High-end construction company needs a business card design

We need a modern looking business card that draws people in, is memorable and looks so good people will want to sick it on their fridges.
On the first side what is needed are:
Logo
My name - Tomasz Brelwik
Title - Managing Director
Website - www.varkelt.co.uk
Email - tomasz@varkelt.co.uk
Telephone - 020 5194 6281
Mobile - 07845139072
On the back side was is needed is a list of all the services we provide:
-Kitchen Renovations
-Bathroom Renovations
-House Renovations
-Garage Conversions
-Extensions
-Loft Conversions
-Conservatories
-Carpentry
-Tiling
-Electrical
-Plumbing & Heating
-Bricklaying
-Landscaping
-Decorating
-Plastering
We would like the colours to be the same shades as on the logo with grey or black for the words.
Target Market(s)
Anyone who needs building work done
Contact Information for Business Card
This business card is for a construction company which strives to deliver excellent service and quality.
The look and feel of the card should represent this.
Requirements
Must have
- On the first side what is needed are:
Logo
My name - Tomasz Brelwik
Title - Managing Director
Website - www.varkelt.co.uk
Email - tomasz@varkelt.co.uk
Telephone - 020 5194 6281
Mobile - 07845139072
Nice to have
- Cool looking features

```html
<!DOCTYPE html>
<html lang="en">
<head>
<meta charset="utf-8">
<title>Varkelt Construction Ltd – Business Card</title>
<link href="https://fonts.googleapis.com/css2?family=Montserrat:wght@400;700;800&family=Saira:wght@300;400&display=swap" rel="stylesheet">
<style>
  :root {
    --bg: #e4e4e4;
    --paper: #ffffff;
    --green: #6cb944;
    --green-dark: #3d8a37;
    --green-deep: #2f7a30;
    --green-light: #82c655;
    --ink: #555a5e;
    --white: #ffffff;
  }
  * { margin: 0; padding: 0; box-sizing: border-box; }
  html, body { width: 1200px; height: 1200px; overflow: hidden; background: var(--bg); }
  body { position: relative; font-family: 'Montserrat', sans-serif; }

  .card { position: absolute; left: 150px; width: 900px; height: 514px; overflow: hidden; box-shadow: 0 14px 28px rgba(0,0,0,.18); }
  .card--front { top: 56px; background: var(--paper); }
  .card--back { top: 630px; background: linear-gradient(135deg, var(--green-deep) 0%, #46923f 55%, #66a262 100%); color: var(--white); }

  /* front */
  .brand { position: absolute; left: 120px; top: 178px; width: 270px; text-align: center; display: flex; align-items: center; gap: 10px; }
  .brand__mark { width: 20px; height: 20px; background: var(--green); flex: none; }
  .brand__name { font-family: 'Saira', sans-serif; font-weight: 400; color: var(--green); font-size: 27px; letter-spacing: 1px; line-height: 1.15; text-align: left; }
  .divider { position: absolute; left: 439px; top: 148px; width: 1px; height: 168px; background: var(--green); }
  .person { position: absolute; left: 490px; top: 148px; }
  .person__name { font-weight: 800; font-size: 34px; color: var(--green); line-height: 1; letter-spacing: .5px; }
  .person__title { font-weight: 700; font-size: 18px; color: var(--green-dark); margin-top: 8px; }
  .contacts { list-style: none; margin-top: 22px; }
  .contacts li { display: flex; align-items: center; gap: 10px; font-size: 20px; color: var(--ink); line-height: 29px; }
  .contacts svg { width: 16px; height: 16px; fill: var(--green-dark); flex: none; }
  .band { position: absolute; left: 0; bottom: 0; width: 100%; height: 66px; background: linear-gradient(90deg, var(--green-deep), #4d9443); }
  .band__accent { position: absolute; right: 0; bottom: 0; width: 900px; height: 66px; }
  .band__url { position: absolute; left: 0; width: 880px; bottom: 0; height: 66px; line-height: 62px; text-align: center; color: var(--white); font-weight: 700; font-size: 22px; letter-spacing: 5px; }

  /* back */
  .back__brand { position: absolute; left: 0; right: 0; top: 100px; text-align: center; }
  .back__brand-name { font-family: 'Saira', sans-serif; font-weight: 400; font-size: 66px; letter-spacing: 6px; line-height: 1; }
  .back__brand-sub { font-family: 'Saira', sans-serif; font-weight: 400; font-size: 20px; letter-spacing: 5px; margin-top: 10px; }
  .back__rule { position: absolute; left: 194px; top: 275px; width: 488px; height: 2px; background: var(--white); }
  .services { position: absolute; left: 0; right: 0; top: 300px; text-align: center; font-family: 'Saira', sans-serif; font-weight: 300; font-size: 20.5px; line-height: 28px; }
  .services__row { display: block; white-space: nowrap; }
  .tick { display: inline-block; width: 15px; height: 15px; vertical-align: -2px; margin: 0 3px 0 4px; }
  .social { position: absolute; left: 0; right: 0; top: 452px; display: flex; justify-content: center; gap: 8px; }
  .social span { width: 27px; height: 27px; border: 2px solid var(--white); border-radius: 6px; }
</style>
</head>
<body>

<section class="card card--front">
  <div class="brand">
    <span class="brand__mark"></span>
    <span class="brand__name">VARKELT<br>CONSTRUCTION LTD</span>
  </div>
  <div class="divider"></div>
  <div class="person">
    <p class="person__name">TOMASZ BRELWIK</p>
    <p class="person__title">MANAGING DIRECTOR</p>
    <ul class="contacts">
      <li><svg viewBox="0 0 24 24"><path d="M6.6 10.8a15 15 0 0 0 6.6 6.6l2.2-2.2c.3-.3.7-.4 1-.2 1.1.4 2.3.6 3.6.6.6 0 1 .4 1 1V20c0 .6-.4 1-1 1A17 17 0 0 1 3 4c0-.6.4-1 1-1h3.5c.6 0 1 .4 1 1 0 1.3.2 2.5.6 3.6.1.3 0 .7-.2 1z"/></svg>020 5194 6281</li>
      <li><svg viewBox="0 0 24 24"><path d="M7 1h10a2 2 0 0 1 2 2v18a2 2 0 0 1-2 2H7a2 2 0 0 1-2-2V3a2 2 0 0 1 2-2zm0 3v14h10V4z"/></svg>07845139072</li>
      <li><svg viewBox="0 0 24 24"><path d="M2 5h20v14H2zm2 2v.5l8 5 8-5V7l-8 5z"/></svg>tomasz@varkelt.co.uk</li>
    </ul>
  </div>
  <div class="band">
    <svg class="band__accent" viewBox="0 0 900 66" preserveAspectRatio="none">
      <polygon points="730,0 900,0 900,66 706,66" fill="#82c655"/>
      <polygon points="721,0 727,0 703,66 697,66" fill="#ffffff"/>
    </svg>
    <p class="band__url">www.varkelt.co.uk</p>
  </div>
</section>

<section class="card card--back">
  <div class="back__brand">
    <p class="back__brand-name">VARKELT</p>
    <p class="back__brand-sub">CONSTRUCTION LTD</p>
  </div>
  <div class="back__rule"></div>
  <p class="services">
    <span class="services__row">Kitchen Renovations<svg class="tick" viewBox="0 0 16 16"><rect x="1" y="1" width="14" height="14" fill="none" stroke="#fff" stroke-width="1.6"/><path d="M4 8l3 3 5-6" fill="none" stroke="#fff" stroke-width="1.8"/></svg>Bathroom Renovations<svg class="tick" viewBox="0 0 16 16"><rect x="1" y="1" width="14" height="14" fill="none" stroke="#fff" stroke-width="1.6"/><path d="M4 8l3 3 5-6" fill="none" stroke="#fff" stroke-width="1.8"/></svg>House Renovations</span>
    <span class="services__row">Garage Conversions<svg class="tick" viewBox="0 0 16 16"><rect x="1" y="1" width="14" height="14" fill="none" stroke="#fff" stroke-width="1.6"/><path d="M4 8l3 3 5-6" fill="none" stroke="#fff" stroke-width="1.8"/></svg>Extensions<svg class="tick" viewBox="0 0 16 16"><rect x="1" y="1" width="14" height="14" fill="none" stroke="#fff" stroke-width="1.6"/><path d="M4 8l3 3 5-6" fill="none" stroke="#fff" stroke-width="1.8"/></svg>Loft Conversions<svg class="tick" viewBox="0 0 16 16"><rect x="1" y="1" width="14" height="14" fill="none" stroke="#fff" stroke-width="1.6"/><path d="M4 8l3 3 5-6" fill="none" stroke="#fff" stroke-width="1.8"/></svg>Conservatories</span>
    <span class="services__row">Carpentry<svg class="tick" viewBox="0 0 16 16"><rect x="1" y="1" width="14" height="14" fill="none" stroke="#fff" stroke-width="1.6"/><path d="M4 8l3 3 5-6" fill="none" stroke="#fff" stroke-width="1.8"/></svg>Tiling<svg class="tick" viewBox="0 0 16 16"><rect x="1" y="1" width="14" height="14" fill="none" stroke="#fff" stroke-width="1.6"/><path d="M4 8l3 3 5-6" fill="none" stroke="#fff" stroke-width="1.8"/></svg>Electrical<svg class="tick" viewBox="0 0 16 16"><rect x="1" y="1" width="14" height="14" fill="none" stroke="#fff" stroke-width="1.6"/><path d="M4 8l3 3 5-6" fill="none" stroke="#fff" stroke-width="1.8"/></svg>Plumbing &amp; Heating<svg class="tick" viewBox="0 0 16 16"><rect x="1" y="1" width="14" height="14" fill="none" stroke="#fff" stroke-width="1.6"/><path d="M4 8l3 3 5-6" fill="none" stroke="#fff" stroke-width="1.8"/></svg>Bricklaying</span>
    <span class="services__row">Landscaping<svg class="tick" viewBox="0 0 16 16"><rect x="1" y="1" width="14" height="14" fill="none" stroke="#fff" stroke-width="1.6"/><path d="M4 8l3 3 5-6" fill="none" stroke="#fff" stroke-width="1.8"/></svg>Decorating<svg class="tick" viewBox="0 0 16 16"><rect x="1" y="1" width="14" height="14" fill="none" stroke="#fff" stroke-width="1.6"/><path d="M4 8l3 3 5-6" fill="none" stroke="#fff" stroke-width="1.8"/></svg>Plastering</span>
  </p>
  <div class="social" aria-label="Social media links">
    <span></span><span></span><span></span>
  </div>
</section>

</body>
</html>
```